professional business card design for technology company

We are a small technology consulting firm, specialising in consulting based around Cloud and Managed services. Our colour scheme is yellow, blue and white, as you can see in the logos. Although we are based in melbourne australia, due to the nature of our work, our clients can be located anywhere. We are looking for a clean, professional, positive look - similar to our company logo

Target Market(s)

small business

Industry/Entity Type

Business

Contact Information for Business Card

eye catching, designed to incorporate some level of raised printing. Must contain website address, phone number, name and job title

Requirements
Must have
• Logo (attached) - use of the same colour scheme

```html
<!DOCTYPE html>
<html lang="en">
<head>
<meta charset="utf-8">
<title>Nubora Business Card</title>
<link href="https://fonts.googleapis.com/css2?family=Montserrat:wght@400;600;700&family=Open+Sans:wght@400;600&display=swap" rel="stylesheet">
<style>
  :root {
    --page: #e6e6e4;
    --card: #f1f1f1;
    --yellow: #f2d200;
    --yellow-deep: #dcc000;
    --charcoal: #2d2d2d;
    --ink: #555555;
    --blue: #2ca3dc;
    --white: #ffffff;
  }
  * { box-sizing: border-box; margin: 0; padding: 0; }
  html, body { width: 1200px; height: 960px; overflow: hidden; background: var(--page); }
  .canvas { position: relative; width: 1200px; height: 960px; }
  .card {
    position: absolute; left: 200px; width: 800px; height: 440px;
    background: var(--card); overflow: hidden;
    box-shadow: 0 6px 18px rgba(0,0,0,.18);
  }
  .card--front { top: 20px; }
  .card--back { top: 500px; }
  .card-shapes { position: absolute; inset: 0; width: 800px; height: 440px; }
  .wordmark {
    position: absolute; display: flex; align-items: center;
    font-family: "Montserrat", sans-serif; font-weight: 700; color: var(--ink);
    letter-spacing: -1px;
  }
  .wordmark-dot { border-radius: 50%; background: var(--blue); flex: none; }
  .card--front .wordmark { left: 0; right: 0; top: 150px; justify-content: center; font-size: 92px; gap: 22px; }
  .card--front .wordmark-dot { width: 56px; height: 56px; }
  .front-url {
    position: absolute; left: 0; right: 0; top: 322px; text-align: center;
    font-family: "Open Sans", sans-serif; font-size: 14px; letter-spacing: 4px; color: var(--ink);
  }
  .card--back .wordmark { left: 70px; top: 300px; font-size: 52px; gap: 14px; }
  .card--back .wordmark-dot { width: 32px; height: 32px; }
  .holder { position: absolute; left: 520px; top: 88px; font-family: "Montserrat", sans-serif; }
  .holder-name { color: var(--white); font-size: 22px; letter-spacing: 1px; font-weight: 400; }
  .holder-name strong { font-weight: 700; }
  .holder-title { color: var(--yellow); font-size: 15px; font-weight: 400; margin-top: 2px; }
  .contact-list { list-style: none; position: absolute; left: 0; top: 0; }
  .contact-item {
    position: absolute; left: 528px; font-family: "Open Sans", sans-serif;
    font-size: 16px; color: var(--white); white-space: nowrap; letter-spacing: .4px;
  }
</style>
</head>
<body>
<main class="canvas">

  <section class="card card--front" aria-label="Card front">
    <svg class="card-shapes" viewBox="0 0 800 440" aria-hidden="true">
      <polygon points="0,0 250,0 0,330" fill="var(--yellow)"/>
      <polygon points="250,0 290,0 0,380 0,330" fill="var(--yellow-deep)" opacity=".55"/>
      <polygon points="800,20 800,440 620,440" fill="var(--yellow)"/>
      <polygon points="800,20 620,440 585,440" fill="var(--yellow-deep)" opacity=".55"/>
    </svg>
    <div class="wordmark"><span class="wordmark-dot"></span>Nubora</div>
    <p class="front-url">www.nubora.com</p>
  </section>

  <section class="card card--back" aria-label="Card back">
    <svg class="card-shapes" viewBox="0 0 800 440" aria-hidden="true">
      <polygon points="150,0 300,0 0,300 0,150" fill="var(--yellow)"/>
      <polygon points="300,0 330,0 0,330 0,300" fill="var(--yellow-deep)" opacity=".6"/>
      <polygon points="480,0 800,0 800,440 400,440" fill="var(--charcoal)"/>
      <line x1="470" y1="66" x2="800" y2="66" stroke="var(--yellow)" stroke-width="2"/>
      <line x1="450" y1="156" x2="800" y2="156" stroke="var(--yellow)" stroke-width="2"/>
      <g class="contact-icons" fill="none" stroke="var(--yellow)" stroke-width="2">
        <rect x="440" y="222" width="26" height="14" fill="var(--yellow)" stroke="none"/>
        <polygon points="478,215 494,215 502,229 494,243 478,243 470,229"/>
        <path d="M481,223 l4,-2 l3,4 l-2,2 q2,4 5,5 l2,-2 l4,3 l-2,4 q-10,-1 -14,-14z" fill="var(--yellow)" stroke="none"/>
        <rect x="430" y="277" width="36" height="14" fill="var(--yellow)" stroke="none"/>
        <polygon points="478,270 494,270 502,284 494,298 478,298 470,284"/>
        <rect x="479" y="278" width="14" height="11" fill="var(--yellow)" stroke="none"/>
        <path d="M479,278 l7,6 l7,-6" stroke="var(--charcoal)" stroke-width="1.5"/>
        <rect x="420" y="332" width="46" height="14" fill="var(--yellow)" stroke="none"/>
        <polygon points="478,325 494,325 502,339 494,353 478,353 470,339"/>
        <circle cx="486" cy="339" r="7" fill="var(--yellow)" stroke="none"/>
        <path d="M480,337 q6,-2 6,-6 M486,346 q0,-4 6,-5" stroke="var(--charcoal)" stroke-width="1.5"/>
      </g>
    </svg>
    <div class="wordmark"><span class="wordmark-dot"></span>Nubora</div>
    <div class="holder">
      <p class="holder-name"><strong>MARCO T.</strong> DELGADO</p>
      <p class="holder-title">PRINCIPAL</p>
    </div>
    <ul class="contact-list">
      <li class="contact-item" style="top:218px">305-555-0142</li>
      <li class="contact-item" style="top:273px">MarcoTDelgado@nubora.com</li>
      <li class="contact-item" style="top:328px">www.nubora.com</li>
    </ul>
  </section>

</main>
</body>
</html>
```